Personal Web page for recruiter and owner of consulting firm

I work full time as a recruiter so I want a page that allows for me to support my efforts. I would like a long single page, I need to be able to upload four two minute videos, and 4 images. I also want the color scheme to match with my consulting company. I own the domain marcusfenwold.net already through wordpress . I took a shot at it myself and its terrible.

Target Market(s)

Potential clients

Industry/Entity Type

Management Consulting

Logo Text

marcus fenwold

Font styles to use
Serif

Requirements
Must have
• Must in color scheme go well with my consulting company logo attached
• Must be able to upload 4 two minute videos and 4 images (photos of me)
• Single long scroll page
• Modern and clean
Nice to have
• Easy for me to update videos images and text without complex coding
Should not have
• I want the design and feel to go well with my logos not exactly replicate it

```html
<!DOCTYPE html>
<html lang="en">
<head>
<meta charset="utf-8">
<title>Marcus Fenwold – Recruiter &amp; Consulting</title>
<link href="https://fonts.googleapis.com/css2?family=Open+Sans:wght@400;600;700&display=swap" rel="stylesheet">
<style>
:root{
  --navy:#1f3f72;
  --band:#2f5592;
  --text:#555b63;
  --muted:#7b8189;
  --grey-bg:#eeeff1;
  --line:#d9dce1;
  --white:#ffffff;
  --accent:#3e8fd0;
}
*{margin:0;padding:0;box-sizing:border-box}
html,body{width:1200px;height:3516px;overflow:hidden}
body{position:relative;font-family:"Open Sans",Arial,sans-serif;color:var(--text);background:var(--white)}
.abs{position:absolute}

/* hero */
.hero{left:0;top:0;width:1200px;height:576px;background:linear-gradient(120deg,#2c3a47 0%,#4f6272 35%,#6c7d88 55%,#3a4855 80%,#28333d 100%);border-top:6px solid var(--accent)}
.hero-shade{left:0;top:0;width:1200px;height:576px;background:linear-gradient(180deg,rgba(10,20,30,.35),rgba(10,20,30,.15) 40%,rgba(10,20,30,.45))}
.brand{left:89px;top:36px;color:var(--white);text-align:center;padding-right:16px;border-right:1px solid rgba(255,255,255,.7)}
.brand-name{font-size:24px;letter-spacing:3px;font-weight:400;line-height:1.1}
.brand-sub{font-size:11px;letter-spacing:3px;margin-top:4px}
.nav{left:340px;top:44px;display:flex;color:var(--white);font-size:15px}
.nav a{color:var(--white);text-decoration:none;padding:4px 14px;margin-right:18px;line-height:20px}
.nav a.current{border:1.5px solid var(--white);border-radius:16px;display:flex;align-items:center;gap:6px}
.hero-title{left:89px;top:392px;color:var(--white)}
.hero-title h1{font-size:44px;font-weight:600;letter-spacing:2px;line-height:1}
.hero-title p{font-size:28px;letter-spacing:1px;margin-top:6px}
.slider-arrows{left:1046px;top:500px;display:flex;gap:8px}
.slider-arrows span{width:28px;height:28px;border-radius:50%;background:rgba(0,0,0,.45);display:flex;align-items:center;justify-content:center}

/* headings */
.section-title{width:1200px;left:0;text-align:center;color:var(--navy);font-size:31px;font-weight:400;letter-spacing:.5px}
.side-title{color:var(--navy);font-size:29px;font-weight:400}

/* welcome */
.intro{left:130px;top:688px;width:940px;text-align:center;font-size:13px;line-height:22px}
.feature{width:290px;text-align:center}
.feature-icon{width:112px;height:112px;margin:0 auto;border-radius:50%;border:3px solid #e6e8eb;display:flex;align-items:center;justify-content:center}
.feature-icon .inner{width:90px;height:90px;border-radius:50%;border:1px solid #e0e3e6;display:flex;align-items:center;justify-content:center}
.feature h3{font-size:16px;font-weight:400;color:#3a3f46;margin-top:30px;letter-spacing:.5px}
.feature p{font-size:11px;line-height:17px;margin:8px auto 0;width:256px;color:var(--muted)}
.read-link{display:inline-block;font-size:11.5px;color:#3a3f46;margin-top:10px;letter-spacing:.5px}

/* videos */
.grey-band{left:0;width:1200px;background:var(--grey-bg)}
.video{border:4px solid var(--white);overflow:hidden;box-shadow:0 1px 3px rgba(0,0,0,.15)}
.video-frame{width:100%;height:100%}
.play{width:62px;height:62px;border-radius:50%;background:rgba(30,30,30,.75);display:flex;align-items:center;justify-content:center}
.player-bar{left:0;bottom:0;width:100%;height:34px;background:rgba(20,30,40,.85);display:flex;align-items:center;padding:0 8px;gap:10px}
.player-bar .btn{width:44px;height:22px;background:#2b3440;border-radius:2px;display:flex;align-items:center;justify-content:center}
.player-bar .track{flex:1;height:6px;background:#4a5663;border-radius:3px;position:relative}
.player-bar .track i{position:absolute;left:0;top:0;height:6px;width:42%;background:var(--accent);border-radius:3px}
.player-bar .hd{color:var(--accent);font-size:12px;font-weight:700;font-style:normal}
.side-tools{right:8px;top:8px;display:flex;flex-direction:column;gap:6px}
.side-tools span{width:28px;height:28px;background:rgba(20,30,40,.8);border-radius:2px}

/* text + media */
.body-copy{font-size:13px;line-height:22px;text-align:justify}
.btn-outline{display:inline-block;border:1.5px solid var(--navy);color:var(--navy);border-radius:18px;font-size:11.5px;padding:6px 14px;letter-spacing:.5px}
.photo{border:4px solid var(--white);box-shadow:0 1px 4px rgba(0,0,0,.2)}

/* testimonial */
.quote-band{left:0;top:2045px;width:1200px;height:298px;background:linear-gradient(90deg,#2a4d86,#34609e 50%,#2c5190)}
.avatar{left:134px;top:2111px;width:164px;height:164px;border-radius:50%;border:4px solid rgba(255,255,255,.85);background:radial-gradient(circle at 50% 45%,#b8c4d1,#6d7f93)}
.quote-mark{left:128px;top:2103px;width:44px;height:44px;border-radius:50%;background:#4a78b8;color:var(--white);font-size:34px;font-weight:700;text-align:center;line-height:54px}
.quote-text{left:322px;top:2114px;width:766px;color:var(--white);font-size:15px;line-height:23.5px}
.quote-author{left:322px;top:2246px;color:var(--white);font-size:14px;line-height:23px}

/* blog */
.post{width:312px;text-align:center}
.post-img{width:312px;height:199px}
.post h4{font-size:15.5px;font-weight:400;color:#2f343b;margin-top:16px}
.post time{display:block;font-size:11.5px;color:var(--muted);margin-top:2px}

/* footer */
.foot-brand{left:94px;top:3310px;text-align:center;color:var(--navy)}
.foot-brand .brand-name{font-size:22px;letter-spacing:2px}
.foot-brand .brand-sub{font-size:10px;color:var(--accent)}
.foot-head{font-size:14px;color:#3a3f46;letter-spacing:.5px}
.foot-list{font-size:11.5px;line-height:22px;color:var(--muted);margin-top:14px}
.subscribe{display:flex;margin-top:16px}
.subscribe input{width:148px;height:32px;border:1px solid var(--line);padding:0 8px;font:11.5px "Open Sans",Arial,sans-serif}
.subscribe button{height:32px;width:58px;border:0;background:var(--navy);color:var(--white);font:11.5px "Open Sans",Arial,sans-serif}
.socials{display:flex;gap:10px;margin-top:18px}
.socials span{width:26px;height:26px;background:#4a4f57;border-radius:4px}
.foot-rule{left:89px;top:3443px;width:1022px;height:1px;background:var(--line)}
.copyright{left:0;top:3462px;width:1200px;text-align:center;font-size:12px;color:#3a3f46}
</style>
</head>
<body>

<!-- hero -->
<div class="abs hero" role="img" aria-label="Photo of a consulting team working together around a laptop in a bright office"></div>
<div class="abs hero-shade"></div>
<div class="abs brand"><div class="brand-name">FENWOLD</div><div class="brand-sub">STRATEGIES</div></div>
<nav class="abs nav">
  <a class="current" href="#"><svg width="14" height="13" viewBox="0 0 14 13"><path d="M7 1 1 6.5h2V12h3V8.5h2V12h3V6.5h2z" fill="#fff"/></svg>HOME</a>
  <a href="#">ABOUT US</a><a href="#">SERVICES</a><a href="#">PROJECTS</a><a href="#">SUPPORTS</a><a href="#">BLOG</a><a href="#">CONTACTS</a>
</nav>
<div class="abs hero-title"><h1>FENWOLD</h1><p>Recruiter and own a consulting firm</p></div>
<div class="abs slider-arrows">
  <span><svg width="10" height="12"><path d="M7 1 2 6l5 5" stroke="#fff" stroke-width="2" fill="none"/></svg></span>
  <span><svg width="10" height="12"><path d="M3 1l5 5-5 5" stroke="#fff" stroke-width="2" fill="none"/></svg></span>
</div>

<!-- welcome -->
<h2 class="abs section-title" style="top:636px">WELCOME TO FENWOLD</h2>
<p class="abs intro">It is a long established fact that a reader will be distracted by the readable content of a page when looking at its layout. The point of using Lorem Ipsum is that it has a more-or-less normal distribution of letters, as opposed to using 'Content here, content here', making it look like readable English. Many desktop publishing packages and web page editors now use Lorem Ipsum as their default model text, and a search</p>

<div class="abs feature" style="left:125px;top:814px">
  <div class="feature-icon"><div class="inner"><svg width="40" height="34" viewBox="0 0 40 34"><rect x="2" y="2" width="36" height="23" rx="2" fill="#3e8fd0"/><rect x="16" y="25" width="8" height="5" fill="#3e8fd0"/><rect x="10" y="30" width="20" height="3" fill="#3e8fd0"/></svg></div></div>
  <h3>NEQUE QUISQUAM</h3>
  <p>Neque porro quisquam est qui dolorem ipsum quia dolor sit amet, consectetur, adipisci velit Ipsum has been the industry's standard dummy</p>
  <span class="read-link">READ MORE »</span>
</div>
<div class="abs feature" style="left:448px;top:814px">
  <div class="feature-icon"><div class="inner"><svg width="40" height="36" viewBox="0 0 40 36"><circle cx="15" cy="20" r="9" fill="none" stroke="#3e8fd0" stroke-width="5" stroke-dasharray="4 3"/><circle cx="15" cy="20" r="3" fill="#3e8fd0"/><circle cx="30" cy="9" r="6" fill="none" stroke="#3e8fd0" stroke-width="4" stroke-dasharray="3 2"/></svg></div></div>
  <h3>PORRO QUISQUAM</h3>
  <p>Neque porro quisquam est qui dolorem ipsum quia dolor sit amet, consectetur, adipisci velit Ipsum has been the industry's standard dummy</p>
  <span class="read-link">READ MORE »</span>
</div>
<div class="abs feature" style="left:793px;top:814px">
  <div class="feature-icon"><div class="inner"><svg width="32" height="38" viewBox="0 0 32 38"><rect x="2" y="2" width="20" height="26" fill="#9fc4e6"/><rect x="10" y="10" width="20" height="26" fill="#3e8fd0"/></svg></div></div>
  <h3>DOLOREM IPSUM</h3>
  <p>Neque porro quisquam est qui dolorem ipsum quia dolor sit amet, consectetur, adipisci velit Ipsum has been the industry's standard dummy</p>
  <span class="read-link">READ MORE »</span>
</div>

<!-- videos -->
<div class="abs grey-band" style="top:1125px;height:480px"></div>
<h2 class="abs section-title" style="top:1175px">OUR VIDEOS</h2>

<div class="abs video" style="left:89px;top:1262px;width:490px;height:278px">
  <div class="video-frame" role="img" aria-label="Video still of a man working at a laptop in an office" style="background:linear-gradient(110deg,#6f8fa8,#c9d6df 45%,#8aa5b8 70%,#46637c)"></div>
  <div class="abs play" style="left:214px;top:94px"><svg width="20" height="22"><path d="M3 1l16 10L3 21z" fill="#fff"/></svg></div>
  <div class="abs side-tools"><span></span><span></span><span></span><span></span></div>
  <div class="abs player-bar"><span class="btn"><svg width="10" height="12"><path d="M1 1l8 5-8 5z" fill="#fff"/></svg></span><span class="track"><i></i></span><i class="hd">HD</i></div>
</div>
<div class="abs video" style="left:621px;top:1262px;width:490px;height:278px">
  <div class="video-frame" role="img" aria-label="Video still of three business people giving a thumbs up" style="background:linear-gradient(110deg,#b9c9d6,#e6ecf1 40%,#7b8ea0 65%,#2e3d4d)"></div>
  <div class="abs play" style="left:214px;top:94px"><svg width="20" height="22"><path d="M3 1l16 10L3 21z" fill="#fff"/></svg></div>
  <div class="abs side-tools"><span></span><span></span><span></span><span></span></div>
  <div class="abs player-bar"><span class="btn"><svg width="10" height="12"><path d="M1 1l8 5-8 5z" fill="#fff"/></svg></span><span class="track"><i></i></span><i class="hd">HD</i></div>
</div>

<!-- what we do -->
<h2 class="abs side-title" style="left:89px;top:1700px">WHAT WE DO</h2>
<p class="abs body-copy" style="left:89px;top:1745px;width:475px">It is a long established fact that a reader will be distracted by the readable content of a page when looking at its layout. The point of using Lorem Ipsum is that it has a more-or-less normal distribution of letters, as opposed to using 'Content here, content here', making it look like readable English. Many desktop publishing packages and web page editors now use Lorem Ipsum as their default model text, and a search for 'lorem ipsum' will uncover many web sites still in their infancy. Various versions have evolved over the years</p>
<span class="abs btn-outline" style="left:89px;top:1919px">READ MORE »</span>
<div class="abs photo" style="left:602px;top:1677px;width:510px;height:305px;background:linear-gradient(115deg,#dfe7ee,#f4f6f8 40%,#8b9aa8 70%,#3f4c5a)" role="img" aria-label="Photo of two business people shaking hands"></div>
<div class="abs play" style="left:826px;top:1794px"><svg width="20" height="22"><path d="M3 1l16 10L3 21z" fill="#fff"/></svg></div>

<!-- testimonial -->
<div class="abs quote-band" role="img" aria-label="Faint city skyline in blue behind the testimonial"></div>
<div class="abs avatar" role="img" aria-label="Portrait photo of the client giving the testimonial"></div>
<div class="abs quote-mark">“</div>
<p class="abs quote-text">It is a long established fact that a reader will be distracted by the readable content of a page when looking at its layout. The point of using Lorem Ipsum is that it has a more-or-less normal distribution of letters, as opposed to using 'Content here, content here', making it look like readable English. Many desktop publishing packages and web page editors now use Lorem Ipsum.</p>
<p class="abs quote-author">Harriet Vale<br>Founder, Bramblecrest</p>

<!-- consulting firm -->
<div class="abs photo" style="left:89px;top:2405px;width:508px;height:302px;background:linear-gradient(110deg,#c7d3de,#eef2f5 35%,#5f7387 65%,#26323f)" role="img" aria-label="Photo of two businessmen reviewing work on a tablet"></div>
<div class="abs play" style="left:312px;top:2520px"><svg width="20" height="22"><path d="M3 1l16 10L3 21z" fill="#fff"/></svg></div>
<h2 class="abs side-title" style="left:633px;top:2432px">CONSULTING FIRM</h2>
<p class="abs body-copy" style="left:633px;top:2474px;width:478px">It is a long established fact that a reader will be distracted by the readable content of a page when looking at its layout. The point of using Lorem Ipsum is that it has a more-or-less normal distribution of letters, as opposed to using 'Content here, content here', making it look like readable English. Many desktop publishing packages and web page editors now use Lorem Ipsum as their default model text, and a search for 'lorem ipsum' will uncover many web sites still in their infancy. Various versions have evolved over the years</p>
<span class="abs btn-outline" style="left:633px;top:2645px">READ MORE »</span>

<!-- blog -->
<div class="abs grey-band" style="top:2768px;height:440px"></div>
<h2 class="abs section-title" style="top:2818px">LATEST BLOG</h2>
<article class="abs post" style="left:89px;top:2890px">
  <div class="post-img" role="img" aria-label="Overhead photo of a team meeting around a table" style="background:linear-gradient(135deg,#8b8070,#c9c2b6 45%,#5b6a78)"></div>
  <h4>Neque porro quisquam est qui</h4><time>19/05/17</time>
</article>
<article class="abs post" style="left:441px;top:2890px">
  <div class="post-img" role="img" aria-label="Photo of business people talking in a bright lobby" style="background:linear-gradient(135deg,#e8ecef,#c8d2da 50%,#4b5562)"></div>
  <h4>Dolorem ipsum quia dolor sit amet</h4><time>17/05/17</time>
</article>
<article class="abs post" style="left:792px;top:2890px">
  <div class="post-img" role="img" aria-label="Photo of colleagues working together at a desk" style="background:linear-gradient(135deg,#6f8aa1,#b8c7d3 45%,#7c8a96)"></div>
  <h4>Quisquam est qui dolorem</h4><time>13/05/17</time>
</article>

<!-- footer -->
<div class="abs foot-brand"><div class="brand-name">FENWOLD</div><div class="brand-sub">STRATEGIES</div></div>
<div class="abs" style="left:342px;top:3256px">
  <div class="foot-head">CONTACT US</div>
  <div class="foot-list">Address : 14 Harlow Lane, Eastgate<br>Kendal, LA9 4QT<br>Phone : +07000 482 615<br>Email : info@marcusfenwold.net</div>
</div>
<div class="abs" style="left:649px;top:3256px">
  <div class="foot-head">JOIN OUR MAILING LIST</div>
  <div class="foot-list" style="width:230px;line-height:17px">Your about us information would fit here nicely.</div>
  <div class="subscribe"><input type="text" placeholder="Email address"><button>Submit</button></div>
</div>
<div class="abs" style="left:930px;top:3256px">
  <div class="foot-head">FOLLOW US OUT THERE</div>
  <div class="socials"><span></span><span></span><span></span><span></span></div>
</div>
<div class="abs foot-rule"></div>
<p class="abs copyright">Copyright © 2017. All Rights Reserved</p>

</body>
</html>
```